Mirel and Dermal Fillers

We need a poster designed to display outside our dental practice to advertise that we offer mirel and dermal fillers

Dental

```html
<!DOCTYPE html>
<html lang="en">
<head>
<meta charset="utf-8">
<title>We Offer Mirel &amp; Derma Fillers</title>
<link rel="stylesheet" href="https://fonts.googleapis.com/css2?family=Cinzel:wght@400&family=Tangerine:wght@400&display=swap">
<style>
  :root {
    --paper: #fdfbf7;
    --paper-warm: #f8f1e6;
    --rose: #e56aa8;
    --ampersand: #b8a07a;
    --blossom-pink: #ef6fa6;
    --blossom-peach: #f3a27c;
    --blossom-cream: #f6ecd9;
  }
  html, body {
    margin: 0;
    padding: 0;
    width: 849px;
    height: 1200px;
    overflow: hidden;
    background: var(--paper);
  }
  .poster {
    position: relative;
    width: 849px;
    height: 1200px;
    overflow: hidden;
    background: radial-gradient(ellipse at 30% 30%, var(--paper) 0%, var(--paper-warm) 100%);
  }
  .headline {
    position: absolute;
    left: 86px;
    top: 66px;
    margin: 0;
    font-family: "Cinzel", serif;
    font-weight: 400;
    color: var(--rose);
    font-size: 150px;
    line-height: 128px;
    letter-spacing: 2px;
  }
  .headline span { display: block; }
  .headline .ampersand {
    position: absolute;
    left: 395px;
    top: 350px;
    font-family: "Tangerine", cursive;
    font-size: 200px;
    line-height: 1;
    color: var(--ampersand);
  }
  .blossom-spray {
    position: absolute;
    inset: 0;
  }
</style>
</head>
<body>
<main class="poster">
  <h1 class="headline">
    <span>We</span>
    <span>Offer</span>
    <span>Mirel</span>
    <span class="ampersand" aria-hidden="true">&amp;</span>
    <span>Derma</span>
    <span>Fillers</span>
  </h1>

  <svg class="blossom-spray" width="849" height="1200" viewBox="0 0 849 1200" role="img" aria-label="Swirling spray of pink, peach and cream blossoms and petals along the lower edge and right side">
    <defs>
      <linearGradient id="sprayBottom" x1="0" y1="0" x2="1" y2="0">
        <stop offset="0" stop-color="var(--blossom-pink)" stop-opacity="0.85"/>
        <stop offset="0.5" stop-color="var(--blossom-peach)" stop-opacity="0.9"/>
        <stop offset="1" stop-color="var(--blossom-pink)" stop-opacity="0.9"/>
      </linearGradient>
      <linearGradient id="sprayRight" x1="0" y1="1" x2="0" y2="0">
        <stop offset="0" stop-color="var(--blossom-peach)" stop-opacity="0.7"/>
        <stop offset="1" stop-color="var(--blossom-cream)" stop-opacity="0"/>
      </linearGradient>
    </defs>
    <path d="M0 1010 C120 980 260 1020 380 990 C520 960 640 900 849 820 L849 1200 L0 1200 Z" fill="url(#sprayBottom)"/>
    <path d="M640 560 C720 520 790 480 849 430 L849 900 C760 920 680 880 620 820 C690 760 700 680 640 560 Z" fill="url(#sprayRight)"/>
  </svg>
</main>
</body>
</html>
```